Brightline Energy Product Distribution Brochure

We are looking to have our current brochure for our customers completely redesigned...the idea is to present the relevant information in an attractive way . Our website is brightlineenergyco.example where you can find more information about us. We have included a file with a rough idea of the page order and what each should include but feel free to adapt based on design. The example provided is only for context and doesnt have to be maintained. We will be using the brochure both digitally and in print form. As long as it reads easily and is eye catching, the design can be horizontal or vertical.Final deliverable should be indesign file.

"Our Brands" page: should be limited to one page (space being enough) where it has the header for each one (for example diesel generators) space for one or two lines of text and then the corresponding logos for each of the five categories
Updates

For those asking: the "our brands" page should be a single page layout where there is a header with the corresponding section and space for maybe one line of text followed by the two logos for that category. Each of the product pages should be similar in fashion to the one in the document attached: a photo of the product with some white space and space for the text to be included. We will be posting additional examples today

Target Market(s)

We want to present it to customers both digitally and in print so they can see our products

Industry/Entity Type

Power Generation

Font styles to use
Serif

Requirements
Must have
• Eye catching and able to present the information in a presentable fashion. Rest is up to you.
Nice to have
• Should incorporate the colors of our logo but can also add other depending on design

```html
<!DOCTYPE html>
<html lang="en">
<head>
<meta charset="utf-8">
<title>Brightline Energy – Product Brochure Spread</title>
<link rel="stylesheet" href="https://fonts.googleapis.com/css2?family=Rubik:wght@800;900&family=Work+Sans:wght@300;400;500&display=swap">
<style>
  :root{
    --stage-bg:#cfd0d2;
    --navy:#0f2c4c;
    --navy-deep:#0a1f38;
    --yellow:#ffc20e;
    --yellow-soft:rgba(255,214,10,.82);
    --orange:#f5a31a;
    --ink:#2b2b2b;
    --white:#ffffff;
    --strip:#4a4a4a;
  }
  *{margin:0;padding:0;box-sizing:border-box}
  html,body{width:1200px;height:801px;overflow:hidden;background:var(--stage-bg)}
  .stage{position:absolute;left:0;top:0;width:1421px;height:948px;transform:scale(.8445);transform-origin:0 0;font-family:"Work Sans",sans-serif;color:var(--ink)}
  .page{position:absolute;top:84px;height:792px;overflow:hidden;background:var(--white)}
  .page--left{left:97px;width:612px}
  .page--right{left:709px;width:614px}
  .abs{position:absolute}
  .photo{position:absolute}
  .photo--refinery-left{left:0;top:0;width:264px;height:784px;background:linear-gradient(180deg,#2c4660 0%,#3d4a55 35%,#6b5a3c 65%,#c9913b 85%,#7a5a2e 100%)}
  .photo--refinery-right{left:0;top:0;width:614px;height:640px;background:linear-gradient(180deg,#143457 0%,#1d3e63 50%,#2a4a6a 100%)}
  .photo--generator{left:235px;top:184px;width:323px;height:210px;background:linear-gradient(180deg,#f4f4f4 0%,#e6e6e6 78%,#1e1e1e 79%,#111 100%);border:1px solid #ddd}
  .photo--alt-small{left:66px;top:214px;width:145px;height:120px;border-radius:10px;background:radial-gradient(circle at 55% 60%,#3a3a3a,#111 75%)}
  .photo--alt-large{left:281px;top:184px;width:315px;height:252px;border-radius:14px;background:radial-gradient(circle at 40% 55%,#3c3c3c,#121212 72%)}
  .shapes{position:absolute;left:0;top:0}
  .eyebrow{font-family:"Work Sans",sans-serif;font-weight:500;font-size:24px;letter-spacing:1px;color:var(--white)}
  .rule{height:4px;width:56px;background:var(--yellow)}
  .title{font-family:"Rubik",sans-serif;font-weight:900;font-size:45px;letter-spacing:.5px;color:var(--yellow);white-space:nowrap;line-height:1}
  .subtitle{font-weight:500;font-size:23px;line-height:29px;letter-spacing:.8px;color:var(--white)}
  .section-head{font-weight:300;font-size:18px;letter-spacing:.5px;color:var(--orange)}
  .features{list-style:none;font-size:10.6px;line-height:13.2px;color:var(--ink)}
  .features li{position:relative;padding-left:16px}
  .features li::before{content:"";position:absolute;left:0;top:4px;width:4px;height:4px;border-radius:50%;background:var(--orange)}
  .body-copy{font-size:10.6px;line-height:13.2px;color:var(--ink)}
  .folio{position:absolute;top:748px;width:98px;height:44px}
  .folio span{position:absolute;top:6px;font-family:"Rubik",sans-serif;font-weight:900;font-size:27px;color:#3a3a3a}
  .base-strip{position:absolute;left:0;bottom:0;width:100%;height:8px;background:var(--strip)}
</style>
</head>
<body>
<div class="stage">

  <!-- Left page: Diesel Generators -->
  <section class="page page--left">
    <div class="photo photo--refinery-left" role="img" aria-label="Photo of an industrial refinery at dusk with lit towers"></div>
    <svg class="shapes" width="612" height="792" viewBox="0 0 612 792">
      <polygon points="0,398 264,276 264,660 0,660" fill="var(--yellow-soft)" opacity=".55"/>
      <polygon points="0,400 264,278 264,330 0,460" fill="var(--yellow)" opacity=".6"/>
    </svg>
    <div class="photo photo--generator" role="img" aria-label="Photo of a white enclosed 100 KW Brightline Energy diesel generator"></div>

    <p class="abs eyebrow" style="left:48px;top:60px">OUR PRODUCT</p>
    <div class="abs rule" style="left:48px;top:95px"></div>
    <h1 class="abs title" style="left:48px;top:106px">DIESEL GENERATORS</h1>
    <p class="abs subtitle" style="left:48px;top:171px">RENTAL<br>GENERATORS</p>

    <h2 class="abs section-head" style="left:288px;top:420px">FEATURES</h2>
    <ul class="abs features" style="left:288px;top:454px;width:300px">
      <li>30 to 500 KW powered by Harlan Field diesel engines. EPA Tier 2, Tier 3 and Tier i4</li>
      <li>13 to 60 KW powered by Kessler diesel engines. EPA Tier i4</li>
      <li>Lemaire Sorel alternators • Stanwick (Cullen Generator Technologies) alternators [optional]</li>
      <li>Deepwell DW 700 series controllers for stand-alone operation • Deepwell DW 800 series controllers for paralleling operation [optional]</li>
      <li>12-Gauge steel enclosures with stainless steel hardware</li>
      <li>12-Gauge 5052 aluminum enclosures with stainless steel hardware [optional]</li>
      <li>Miraquiet Hush QX critical grade silencers</li>
      <li>Delvane manual main line circuit breakers</li>
      <li>ACR manual and motorized main line circuit breakers [optional]</li>
      <li>50 to 5000-Gal, single-wall fuel tanks</li>
      <li>50 to 5000-Gal, double-walled SL142 listed fuel tanks</li>
      <li>Battery disconnect switch</li>
      <li>12V starting battery</li>
    </ul>

    <div class="folio" style="left:24px">
      <svg width="98" height="44" viewBox="0 0 98 44"><polygon points="22,0 98,0 76,44 0,44" fill="var(--yellow)"/></svg>
      <span style="left:14px">08</span>
    </div>
    <div class="base-strip"></div>
  </section>

  <!-- Right page: AC Alternators -->
  <section class="page page--right">
    <div class="photo photo--refinery-right" role="img" aria-label="Photo of refinery towers and pipework under a blue tint"></div>
    <svg class="shapes" width="614" height="792" viewBox="0 0 614 792">
      <polygon points="614,72 614,276 60,276" fill="var(--yellow-soft)"/>
      <polygon points="43,274 614,274 614,792 43,792" fill="var(--white)"/>
      <polygon points="0,640 43,620 43,792 0,792" fill="var(--white)"/>
    </svg>
    <div class="photo photo--alt-small" role="img" aria-label="Photo of a compact black AC alternator"></div>
    <div class="photo photo--alt-large" role="img" aria-label="Photo of a large black AC alternator"></div>

    <p class="abs eyebrow" style="left:44px;top:60px">OUR PRODUCT</p>
    <div class="abs rule" style="left:44px;top:95px"></div>
    <h1 class="abs title" style="left:43px;top:106px">AC ALTERNATORS</h1>

    <h2 class="abs section-head" style="left:72px;top:361px">DESCRIPTION</h2>
    <p class="abs body-copy" style="left:72px;top:398px;width:200px">Lorem ipsum dolor sit amet, consectetuer adipiscing elit, sed diam nonummy nibh euismod tincidunt ut laoreet dolore magna aliquam erat volutpat. Ut wisi enim ad minim veniam, quis nostrud exerci tation ullamcorper suscipit lobortis nisl ut aliquip ex ea commodo consequat. Duis autem vel eum iriure dolor in hendrerit in vulputate velit esse molestie consequat, vel illum dolore eu feugiat nulla facilisis at vero eros et accumsan et iusto odio dignissim qui blandit praesent luptatum zzril delenit augue duis dolore te feugait nulla facilisi.</p>
    <p class="abs body-copy" style="left:315px;top:485px;width:264px">Lorem ipsum dolor sit amet, consectetuer adipiscing elit, sed diam nonummy nibh euismod tincidunt ut laoreet dolore magna aliquam erat volutpat. Ut wisi enim ad minim veniam, quis nostrud exerci tation ullamcorper suscipit lobortis nisl ut aliquip ex ea commodo consequat. Duis autem vel eum iriure dolor in hendrerit in vulputate velit esse molestie consequat.</p>
    <p class="abs body-copy" style="left:129px;top:650px;width:448px">Lorem ipsum dolor sit amet, consectetuer adipiscing elit, sed diam nonummy nibh euismod tincidunt ut laoreet dolore magna aliquam erat volutpat. Ut wisi enim ad minim veniam, quis nostrud exerci tation ullamcorper suscipit lobortis nisl ut aliquip ex ea commodo consequat. Duis autem vel eum iriure dolor in hendrerit in vulputate velit esse molestie consequat, vel illum dolore eu feugiat nulla facilisis at vero eros et accumsan et iusto odio dignissim qui blandit praesent luptatum zzril delenit augue duis dolore te feugait nulla facilisi.</p>

    <div class="folio" style="left:3px">
      <svg width="98" height="44" viewBox="0 0 98 44"><polygon points="22,0 98,0 76,44 0,44" fill="var(--yellow)"/></svg>
      <span style="left:33px">09</span>
    </div>
    <div class="base-strip"></div>
  </section>

</div>
</body>
</html>
```